LM-Steuerberatung WordPress Site fully implemented (tax advisor)

Hello!
I need a little Wordpress Site for my newly founded Tax-Advisor Company.
I am a one-man Office advising in the area of Crypto-Currency.
PLEASE only provide a Design, if you can also Implement a WP-Site afterwards on an existing Webspace.

Please find the Content and Website-Description in the attached Document

Language for the Website is German (for now)

Target Market(s)

Tax-Advisory (specialized in Crypto Currency)

Coding

Coded - Design and coding required

Number of Pages Required

5+ page

Font styles to use
Sans Serif

Requirements
Must have
• Wordpress Implementation afterwards - Details according to attached Project Information Document

```html
<!DOCTYPE html>
<html lang="de">
<head>
<meta charset="utf-8">
<title>Leistungen – LM-Steuerberatung</title>
<link href="https://fonts.googleapis.com/css2?family=Manrope:wght@400;500;600;700&display=swap" rel="stylesheet">
<style>
:root{
  --navy:#1b2a40;
  --footer:#161d29;
  --text:#3d4450;
  --white:#ffffff;
  --muted:#c9ced6;
  --line:#3a4354;
  --accent:#2a5aa8;
}
*{margin:0;padding:0;box-sizing:border-box}
html,body{width:908px;height:1200px;overflow:hidden}
body{font-family:'Manrope',sans-serif;color:var(--text);background:var(--white);position:relative}
.topbar{position:absolute;top:0;left:0;width:908px;height:39px;background:var(--navy);color:var(--white);font-size:11.5px}
.topbar .social{position:absolute;left:75px;top:14px;display:flex;gap:12px}
.dot{width:10px;height:10px;background:var(--white);border-radius:50%;display:block}
.topbar .contact{position:absolute;right:75px;top:12px;display:flex;gap:14px;align-items:center}
.topbar .contact span{display:flex;align-items:center;gap:5px}
.header{position:absolute;top:39px;left:0;width:908px;height:69px;background:var(--white)}
.brand{position:absolute;left:75px;top:22px;display:flex;align-items:center;gap:8px;font-weight:700;font-size:14px;color:var(--navy);letter-spacing:.5px}
.brand .mark{width:22px;height:22px;background:var(--navy);display:block}
.nav{position:absolute;top:0;left:0}
.nav .link{position:absolute;top:25px;font-size:12px;font-weight:500;color:var(--navy);text-decoration:none;transform:translateX(-50%);white-space:nowrap}
.nav .link.active::after{content:"";position:absolute;left:50%;top:20px;width:4px;height:4px;margin-left:-2px;border-radius:50%;background:var(--navy)}
.nav .btn{position:absolute;left:738px;top:17px;width:96px;height:33px;background:var(--navy);color:var(--white);border-radius:12px 0 12px 0;font-weight:600;font-size:12px;display:flex;align-items:center;justify-content:center;text-decoration:none;white-space:nowrap}
.hero{position:absolute;top:108px;left:0;width:908px;height:174px;background:linear-gradient(100deg,#4d5561 0%,#7a808a 45%,#9aa0a8 70%,#5f656e 100%);display:flex;align-items:center;justify-content:center}
.hero h1{color:var(--white);font-size:29px;font-weight:700;letter-spacing:-.5px}
.intro{position:absolute;top:336px;left:75px;width:760px;font-size:12.3px;line-height:21px}
.visual{position:absolute;left:75px;top:409px;width:328px;height:308px;border-radius:26px;background:linear-gradient(150deg,#13256e 0%,#1e4fb0 45%,#2f8be0 80%,#55c0f5 100%)}
.services{position:absolute;left:433px;top:415px;width:402px;list-style:none;font-size:12.3px;line-height:21px}
.services li{position:relative;padding-left:12px;margin-bottom:6px}
.services li svg{position:absolute;left:0;top:7px}
.outro{position:absolute;top:746px;left:75px;width:760px;font-size:12.3px;line-height:21px}
.cta{position:absolute;left:76px;top:804px;width:284px;height:39px;background:var(--navy);color:var(--white);border-radius:14px 0 14px 0;display:flex;align-items:center;justify-content:center;gap:8px;font-weight:600;font-size:13px;text-decoration:none}
.footer{position:absolute;top:909px;left:0;width:908px;height:291px;background:var(--footer);color:var(--muted)}
.footer .brand{top:62px;left:75px;color:var(--white);font-size:16px}
.footer .brand .mark{width:26px;height:26px;background:var(--white)}
.footer .tagline{position:absolute;left:75px;top:105px;width:240px;font-size:12.3px;line-height:19.5px}
.footer .social{position:absolute;left:75px;top:186px;display:flex;gap:20px}
.footer .divider{position:absolute;top:59px;width:1px;height:157px;background:var(--line)}
.footer .divider::before{content:"";position:absolute;left:-3px;top:26px;width:3px;height:16px;background:var(--accent)}
.footer h3{position:absolute;top:68px;color:var(--white);font-size:13px;font-weight:700}
.links{position:absolute;left:464px;top:95px;list-style:none;font-size:12.3px}
.links li{height:29.3px}
.contacts{position:absolute;left:686px;top:95px;list-style:none;font-size:12.3px}
.contacts li{height:29.3px;display:flex;align-items:center;gap:8px;margin-top:-5px}
.footer .rule{position:absolute;left:73px;top:245px;width:760px;height:1px;background:var(--line)}
.copy{position:absolute;top:268px;left:0;width:908px;text-align:center;font-size:11px}
.copy strong{color:var(--white);font-weight:600}
</style>
</head>
<body>
<div class="topbar">
  <div class="social" aria-label="Soziale Netzwerke"><span class="dot"></span><span class="dot"></span><span class="dot"></span></div>
  <div class="contact">
    <span><svg width="11" height="11" viewBox="0 0 24 24"><path fill="#fff" d="M6.6 10.8a15 15 0 0 0 6.6 6.6l2.2-2.2c.3-.3.7-.4 1-.2 1.1.4 2.3.6 3.6.6.6 0 1 .4 1 1V20c0 .6-.4 1-1 1C10.6 21 3 13.4 3 4c0-.6.4-1 1-1h3.5c.6 0 1 .4 1 1 0 1.3.2 2.5.6 3.6.1.3 0 .7-.2 1z"/></svg>+43 512 000 471</span>
    <span><svg width="12" height="10" viewBox="0 0 24 18"><path fill="#fff" d="M0 2l12 8 12-8V0H0zM0 4.5V18h24V4.5l-12 8z"/></svg>office@lm-steuer.example</span>
  </div>
</div>
<header class="header">
  <div class="brand"><span class="mark"></span>LM STEUERBERATUNG</div>
  <nav class="nav">
    <a class="link" style="left:422px">Home</a>
    <a class="link active" style="left:503px">Leistungen</a>
    <a class="link" style="left:595px">Über mich</a>
    <a class="link" style="left:688px">Impressum</a>
    <a class="btn">Kontakt</a>
  </nav>
</header>
<section class="hero" role="img" aria-label="Foto: Hände mit Stift und Tablet über Finanzdiagrammen am Schreibtisch">
  <h1>LEISTUNGEN</h1>
</section>
<p class="intro">Ich biete in meiner Kanzlei ausschließlich Spezialberatung rund um die komplexen und vielseitigen Themen im Krypto-Bereich sowie deren Besteuerung, bzw. der Besteuerung und steuerlichen Optimierung von anderen passiven Einkommensmodellen an:</p>
<div class="visual" role="img" aria-label="Illustration: Hand schreibt auf Dokument, darüber steigendes Balkendiagramm in Blautönen"></div>
<ul class="services">
  <li><svg width="7" height="9" viewBox="0 0 7 10"><path d="M1 1l4 4-4 4" stroke="#1b2a40" stroke-width="1.6" fill="none"/></svg>Steueroptimales Besitzen von KryptoAssets auf<br>in- und ausländischen Börsen</li>
  <li><svg width="7" height="9" viewBox="0 0 7 10"><path d="M1 1l4 4-4 4" stroke="#1b2a40" stroke-width="1.6" fill="none"/></svg>Hilfestellung bei der Dokumentation der Einkünfte (Verwendung von Tax-Tools und Aufbereitung der Daten, etc.)</li>
  <li><svg width="7" height="9" viewBox="0 0 7 10"><path d="M1 1l4 4-4 4" stroke="#1b2a40" stroke-width="1.6" fill="none"/></svg>Finanzstrafrechtliche Offenlegung und Aufarbeitung bei Einkünften die nicht ordnungsgemäß erklärt wurden</li>
  <li><svg width="7" height="9" viewBox="0 0 7 10"><path d="M1 1l4 4-4 4" stroke="#1b2a40" stroke-width="1.6" fill="none"/></svg>Beratung rund um das Thema Wegzug, Wohnsitzverlegung und in-/ausländische Gesellschaften</li>
  <li><svg width="7" height="9" viewBox="0 0 7 10"><path d="M1 1l4 4-4 4" stroke="#1b2a40" stroke-width="1.6" fill="none"/></svg>Hilfe bei der korrekten Erklärung der Crypto-Einkünfte und Erstellung der Steuererklärungen</li>
  <li><svg width="7" height="9" viewBox="0 0 7 10"><path d="M1 1l4 4-4 4" stroke="#1b2a40" stroke-width="1.6" fill="none"/></svg>Beratung bei der Unterscheidung und Besteuerung der diversen</li>
  <li><svg width="7" height="9" viewBox="0 0 7 10"><path d="M1 1l4 4-4 4" stroke="#1b2a40" stroke-width="1.6" fill="none"/></svg>Einkunftsmöglichkeiten (Trading, Staking, Lending, Mining, Nodes, NFTs, etc.)</li>
</ul>
<p class="outro">Werden neben der Spezialberatung auch noch klassische Services wie Buchhaltung, Lohnverrechnung etc. benötigt, kann dies gerne über Partner-Kanzleien von mir organisiert werden.</p>
<a class="cta">Nehmen sie gerne Kontakt mit mir auf!
  <svg width="12" height="12" viewBox="0 0 12 12"><circle cx="6" cy="6" r="6" fill="#fff"/><path d="M5 3.5L7.5 6 5 8.5" stroke="#1b2a40" stroke-width="1.6" fill="none"/></svg></a>
<footer class="footer">
  <div class="brand"><span class="mark"></span>LM STEUERBERATUNG</div>
  <p class="tagline">Ihrem Spezialisten bei allen steuerlichen Themen rund um Einkünfte &amp; Vermögen aus Krypto-Assets.</p>
  <div class="social" aria-label="Soziale Netzwerke"><span class="dot" style="width:12px;height:12px"></span><span class="dot" style="width:12px;height:12px"></span><span class="dot" style="width:12px;height:12px"></span></div>
  <div class="divider" style="left:389px"></div>
  <div class="divider" style="left:621px"></div>
  <h3 style="left:464px">QUICK LINKS</h3>
  <ul class="links"><li>Home</li><li>Leistungen</li><li>Über mich</li><li>Impressum</li><li>Kontakt</li></ul>
  <h3 style="left:686px">CONTACT US</h3>
  <ul class="contacts">
    <li><svg width="12" height="9" viewBox="0 0 24 18"><path fill="#9aa1ac" d="M0 2l12 8 12-8V0H0zM0 4.5V18h24V4.5l-12 8z"/></svg>office@lm-steuer.example</li>
    <li><svg width="11" height="11" viewBox="0 0 24 24"><path fill="#9aa1ac" d="M6.6 10.8a15 15 0 0 0 6.6 6.6l2.2-2.2c.3-.3.7-.4 1-.2 1.1.4 2.3.6 3.6.6.6 0 1 .4 1 1V20c0 .6-.4 1-1 1C10.6 21 3 13.4 3 4c0-.6.4-1 1-1h3.5c.6 0 1 .4 1 1 0 1.3.2 2.5.6 3.6.1.3 0 .7-.2 1z"/></svg>+43 512 000 471</li>
  </ul>
  <div class="rule"></div>
  <p class="copy">© 2022 <strong>LM-Steuerberatung</strong>. All right reserved</p>
</footer>
</body>
</html>
```